Professional Business Card - TWO SIDES

I need a new business card design to be used by myself and my employees. I would like a professional card and for the front I thought I would like a dark blue thatch with our logo in a raised gold foil on top of it. On the other side I would like name, position, and contact info. I've uploaded our old design for an example of the info used.

Target Market(s)

Business Clients

Industry/Entity Type

CPA Firm

Contact Information for Business Card

Logo, Name, Title, Address, Phone Numbers, Website address, Email Address

Font styles to use
Serif
Sans Serif

Colors
0054AA
0677BA
7BADD7
CADEEF
E8F1F8
0094D4
00A9DD
6FCCEA
C7EBF8
E9F6FB

Requirements
Must have
• Modern Professional Look
Nice to have
• Logo in Gold Foil or ability to have is raised. I like our logo in a single color
Should not have
• I've uploaded old business card

```html
<!DOCTYPE html>
<html lang="en">
<head>
<meta charset="utf-8">
<title>Hartwell &amp; Hartwell CPA – Business Card</title>
<link rel="stylesheet" href="https://fonts.googleapis.com/css2?family=Arimo:wght@400;700&display=swap">
<style>
  :root {
    --navy: #0b3a6f;
    --navy-soft: #0f4682;
    --white: #ffffff;
    --page: #e6e8ec;
    --ink: #0b3a6f;
  }
  * { box-sizing: border-box; margin: 0; padding: 0; }
  html, body { width: 1200px; height: 900px; overflow: hidden; }
  body {
    background: var(--page);
    font-family: "Arimo", Arial, sans-serif;
    position: relative;
  }
  .card {
    position: absolute;
    width: 540px;
    height: 310px;
    border-radius: 22px;
    overflow: hidden;
    box-shadow: 0 10px 28px rgba(0,0,0,.18);
  }
  .card-info { left: 90px; top: 120px; background: var(--white); }
  .card-brand { left: 570px; top: 470px; background: var(--navy); }

  .info-band {
    position: absolute;
    left: 0; right: 0; top: 150px; bottom: 0;
    background: linear-gradient(180deg, var(--navy-soft), var(--navy));
  }

  .wordmark {
    position: absolute;
    left: 0; right: 0;
    display: flex;
    align-items: center;
    justify-content: center;
    gap: 10px;
    font-weight: 700;
    white-space: nowrap;
    text-align: center;
  }
  .wordmark-dot { width: 14px; height: 14px; flex: none; }
  .wordmark-name { display: block; font-size: 30px; line-height: 1; letter-spacing: .5px; }
  .wordmark-sub { display: block; font-size: 12px; letter-spacing: 3px; margin-top: 6px; }

  .card-info .wordmark { top: 52px; color: var(--ink); }
  .card-info .wordmark-dot { background: var(--ink); }

  .card-brand .wordmark { top: 124px; color: var(--white); }
  .card-brand .wordmark-name { font-size: 32px; }
  .card-brand .wordmark-sub { font-size: 13px; }
  .card-brand .wordmark-dot { background: var(--white); }

  .person {
    position: absolute;
    left: 60px; top: 186px;
    width: 180px;
    text-align: right;
    color: var(--white);
  }
  .person-name { font-size: 21px; font-weight: 700; }
  .person-role { font-size: 13px; margin-top: 4px; }
  .divider {
    position: absolute;
    left: 256px; top: 176px;
    width: 1px; height: 58px;
    background: rgba(255,255,255,.6);
  }
  .contacts {
    position: absolute;
    left: 272px; top: 172px;
    list-style: none;
    color: var(--white);
    font-size: 12.5px;
  }
  .contacts li { display: flex; align-items: center; gap: 8px; height: 21px; }
  .contacts svg { width: 11px; height: 11px; flex: none; }
  .address {
    position: absolute;
    left: 0; right: 0; top: 266px;
    text-align: center;
    color: var(--white);
    font-size: 12.5px;
  }
</style>
</head>
<body>

<section class="card card-info" aria-label="Card front with contact details">
  <div class="info-band" role="img" aria-label="Navy decorative band with accent lines"></div>

  <div class="wordmark">
    <span class="wordmark-dot"></span>
    <span>
      <span class="wordmark-name">HARTWELL &amp; HARTWELL</span>
      <span class="wordmark-sub">CERTIFIED PUBLIC ACCOUNTANTS</span>
    </span>
  </div>

  <div class="person">
    <p class="person-name">Daniel Reyes</p>
    <p class="person-role">Manager</p>
  </div>
  <div class="divider"></div>
  <ul class="contacts">
    <li>
      <svg viewBox="0 0 12 12"><path d="M2.5 1 L4.5 1 L5.3 3.4 L4 4.4 Q5 6.8 7.6 8 L8.6 6.7 L11 7.5 L11 9.5 Q10.5 11 9 11 Q1 10 1 2.5 Q1 1 2.5 1Z" fill="#fff"/></svg>
      555-014-2100
    </li>
    <li>
      <svg viewBox="0 0 12 12"><rect x="1" y="2.5" width="10" height="7" fill="none" stroke="#fff" stroke-width="1.2"/><path d="M1 2.5 L6 6.5 L11 2.5" fill="none" stroke="#fff" stroke-width="1.2"/></svg>
      info@hartwellcpa.com
    </li>
    <li>
      <svg viewBox="0 0 12 12"><circle cx="6" cy="6" r="5" fill="none" stroke="#fff" stroke-width="1.1"/><ellipse cx="6" cy="6" rx="2.2" ry="5" fill="none" stroke="#fff" stroke-width="1"/><path d="M1 6 H11" stroke="#fff" stroke-width="1"/></svg>
      www.hartwellcpa.com
    </li>
  </ul>
  <p class="address">Your address, city, state, ZIP 0000</p>
</section>

<section class="card card-brand" aria-label="Card back with firm name">
  <div class="wordmark">
    <span class="wordmark-dot"></span>
    <span>
      <span class="wordmark-name">HARTWELL &amp; HARTWELL</span>
      <span class="wordmark-sub">CERTIFIED PUBLIC ACCOUNTANTS</span>
    </span>
  </div>
</section>

</body>
</html>
```